Business Postcard Design for Personal Training Company

Need a postcard design for my company called "Copperleaf Studio" Colors are Navy Blue, Blue, Grey and White.

On the front I want there to be pictures and it to feature a box that says "Free Consultation + 50% off your first session!"

And somehow to feature the following phrases " Lose Weight. Gain Muscle."
"Customized Personal training using Q-Pulse, the latest technology in fitness. Reach your fitness goals in just two 25-min sessions per week"

Also want featured the following phrases (maybe on back):

"up to 18 times more effective than a conventional gym workout"

I need the back of the postcard to have all my business information:

Address: 287 Wendover Ln, Building D Suite 318, Fernhollow Bay 40512
Website: copperleaf-studio.example
Phone #: (555) 555-0137
E-mail: copperleafwellness@mailbox.example

I am going to upload my logo, before and after pictures and pictures of people training on the device. Feel free to use as many/or little photos as you want.

Target Market(s)

Wealthy Adults 40+ years old looking for a personal trainer

Industry/Entity Type

Personal Trainer

Colors
0455a3
85cae6
aaaaaa
ffffff

Requirements
Must have
• At least two of the before and after photos, and two or more photos of people working out on the device.

```html
<!DOCTYPE html>
<html lang="en">
<head>
<meta charset="utf-8">
<title>Copperleaf Studio Postcard</title>
<link rel="stylesheet" href="https://fonts.googleapis.com/css2?family=Archivo+Black&family=Archivo+Narrow:wght@600&family=Oswald:wght@400;500;600&family=Lato:wght@400;700&display=swap">
<style>
  :root {
    --blue: #3a9fd6;
    --sky: #85cae6;
    --navy: #0455a3;
    --grey: #aaaaaa;
    --ink: #222222;
    --charcoal: #4a4a4a;
    --band: #2b2b2b;
    --white: #ffffff;
    --page: #e4e4e4;
  }
  * { margin: 0; padding: 0; box-sizing: border-box; }
  html, body { width: 1200px; height: 1200px; overflow: hidden; }
  body { background: var(--page); position: relative; font-family: "Lato", sans-serif; }

  .postcard { position: absolute; left: 270px; width: 660px; height: 512px; overflow: hidden; background: var(--white); }
  .postcard--front { top: 40px; }
  .postcard--back { top: 648px; }
  .postcard__art { position: absolute; inset: 0; width: 660px; height: 512px; }

  .brand { position: absolute; display: flex; align-items: center; gap: 7px; }
  .brand__dot { width: 12px; height: 12px; border-radius: 50%; background: var(--blue); }
  .brand__name { font-family: "Lato", sans-serif; font-weight: 700; font-size: 15px; letter-spacing: 1px; color: #666; white-space: nowrap; }
  .postcard--front .brand { left: 34px; top: 100px; }
  .postcard--back .brand { left: 56px; top: 54px; }

  .headline { position: absolute; left: 32px; line-height: 1; color: var(--blue); font-family: "Archivo Black", sans-serif; }
  .headline--lose { top: 190px; font-size: 76px; letter-spacing: 1px; }
  .headline--weight { top: 256px; font-size: 49px; letter-spacing: 1px; }
  .rule { position: absolute; left: 32px; width: 232px; height: 2px; background: var(--charcoal); }
  .rule--top { top: 303px; }
  .rule--bottom { top: 356px; }
  .headline--gain { top: 306px; left: 32px; width: 232px; font-family: "Oswald", sans-serif; font-weight: 600; font-size: 43px; color: var(--charcoal); letter-spacing: -1px; white-space: nowrap; }
  .intro { position: absolute; left: 32px; top: 382px; width: 275px; font-size: 15px; line-height: 19.5px; color: var(--ink); }

  .offer { position: absolute; left: 362px; top: 322px; width: 200px; text-align: center; color: var(--white); font-family: "Oswald", sans-serif; line-height: 1; }
  .offer__small { font-size: 17px; font-weight: 500; }
  .offer__big { font-size: 46px; font-weight: 500; margin: 4px 0 6px; }

  .claim { position: absolute; left: 30px; width: 250px; text-align: center; line-height: 1; white-space: nowrap; }
  .claim--blue { font-family: "Archivo Narrow", sans-serif; font-weight: 600; font-size: 35px; color: var(--blue); }
  .claim--dark { font-family: "Archivo Black", sans-serif; color: var(--charcoal); }
  .claim--1 { top: 124px; }
  .claim--2 { top: 158px; }
  .claim--3 { top: 196px; font-size: 31px; }
  .claim--4 { top: 234px; font-size: 27px; }
  .claim--5 { top: 266px; font-size: 27px; }

  .contact-bar { position: absolute; left: 0; top: 313px; width: 282px; height: 22px; background: var(--blue); color: var(--white); font-weight: 700; font-size: 17px; line-height: 22px; padding-left: 32px; }
  .contact-list { position: absolute; left: 22px; top: 345px; list-style: none; font-size: 15px; color: var(--ink); }
  .contact-list li { display: flex; align-items: flex-start; gap: 8px; line-height: 20px; margin-bottom: 5px; }
  .contact-list svg { flex: none; margin-top: 4px; }
  .contact-list .email { font-size: 12.5px; letter-spacing: -0.1px; }

  .label { position: absolute; font-family: "Lato", sans-serif; font-weight: 700; font-size: 17px; color: var(--blue); }
</style>
</head>
<body>

<section class="postcard postcard--front" aria-label="Postcard front">
  <svg class="postcard__art" viewBox="0 0 660 512">
    <defs>
      <linearGradient id="paper" x1="0" y1="0" x2="1" y2="1">
        <stop offset="0" stop-color="#ffffff"/><stop offset="1" stop-color="#e9e9e9"/>
      </linearGradient>
      <linearGradient id="greyField" x1="0" y1="0" x2="1" y2="1">
        <stop offset="0" stop-color="#9e9e9e"/><stop offset="1" stop-color="#d8d8d8"/>
      </linearGradient>
      <linearGradient id="photoTones" x1="0" y1="0" x2="0" y2="1">
        <stop offset="0" stop-color="#c9ccd0"/><stop offset="0.45" stop-color="#8a9694"/><stop offset="1" stop-color="#4f7a3c"/>
      </linearGradient>
      <radialGradient id="badgeCore" cx="0.5" cy="0.45" r="0.6">
        <stop offset="0" stop-color="#5ab3e0"/><stop offset="1" stop-color="#1e7fbf"/>
      </radialGradient>
      <clipPath id="heroClip"><circle cx="500" cy="150" r="214"/></clipPath>
    </defs>
    <rect width="660" height="512" fill="url(#paper)"/>
    <path d="M290 0 Q380 230 560 512 L660 512 L660 0 Z" fill="url(#greyField)"/>
    <path d="M212 0 Q300 120 336 250 Q312 110 248 0 Z" fill="var(--blue)"/>
    <path d="M400 512 Q540 450 660 478 L660 512 Z" fill="var(--blue)"/>
    <path d="M440 512 Q560 470 660 492 L660 512 Z" fill="#ffffff"/>
    <circle cx="500" cy="150" r="222" fill="none" stroke="var(--blue)" stroke-width="8"/>
    <g clip-path="url(#heroClip)">
      <rect x="280" y="-70" width="440" height="440" fill="url(#photoTones)" role="img" aria-label="Photo of a client jumping in a training suit beside a trainer on a hillside terrace above a harbour"/>
    </g>
    <g transform="translate(462 373)" fill="var(--blue)">
      <rect x="-84" y="-84" width="168" height="168"/>
      <rect x="-84" y="-84" width="168" height="168" transform="rotate(15)"/>
      <rect x="-84" y="-84" width="168" height="168" transform="rotate(30)"/>
      <rect x="-84" y="-84" width="168" height="168" transform="rotate(45)"/>
      <rect x="-84" y="-84" width="168" height="168" transform="rotate(60)"/>
      <rect x="-84" y="-84" width="168" height="168" transform="rotate(75)"/>
      <circle r="98" fill="url(#badgeCore)"/>
    </g>
    <rect y="494" width="660" height="18" fill="var(--band)"/>
  </svg>

  <div class="brand"><span class="brand__dot"></span><span class="brand__name">COPPERLEAF STUDIO</span></div>
  <h1 class="headline headline--lose">LOSE</h1>
  <div class="headline headline--weight">WEIGHT</div>
  <div class="rule rule--top"></div>
  <div class="headline headline--gain">GAIN MUSCLE</div>
  <div class="rule rule--bottom"></div>
  <p class="intro">Customized Personal training using Q-Pulse, the latest technology in fitness. Reach your fitness goals in just two 25-min sessions per week</p>

  <div class="offer">
    <div class="offer__small">FREE CONSULTATION &amp;</div>
    <div class="offer__big">50% OFF</div>
    <div class="offer__small">YOUR FIRST SESSION!</div>
  </div>
</section>

<section class="postcard postcard--back" aria-label="Postcard back">
  <svg class="postcard__art" viewBox="0 0 660 512">
    <defs>
      <linearGradient id="paperBack" x1="0" y1="0" x2="1" y2="0">
        <stop offset="0" stop-color="#e8e8e8"/><stop offset="0.5" stop-color="#ffffff"/>
      </linearGradient>
      <linearGradient id="blueField" x1="0" y1="0" x2="1" y2="1">
        <stop offset="0" stop-color="#3a9fd6"/><stop offset="1" stop-color="#2a8cc8"/>
      </linearGradient>
      <linearGradient id="bodyTones" x1="0" y1="0" x2="0" y2="1">
        <stop offset="0" stop-color="#e7e3dc"/><stop offset="0.5" stop-color="#c9a488"/><stop offset="1" stop-color="#2e2e33"/>
      </linearGradient>
      <linearGradient id="gymTones" x1="0" y1="0" x2="0" y2="1">
        <stop offset="0" stop-color="#d9dde2"/><stop offset="0.55" stop-color="#5c6470"/><stop offset="1" stop-color="#4a78c0"/>
      </linearGradient>
      <linearGradient id="portraitTones" x1="0" y1="0" x2="1" y2="0">
        <stop offset="0" stop-color="#2f6f9a"/><stop offset="0.5" stop-color="#b88d74"/><stop offset="1" stop-color="#3d8fb5"/>
      </linearGradient>
    </defs>
    <rect width="660" height="512" fill="url(#paperBack)"/>
    <path d="M300 0 Q372 110 352 512 L660 512 L660 0 Z" fill="#ffffff"/>
    <path d="M300 0 Q372 110 352 512 L372 512 Q392 100 322 0 Z" fill="var(--blue)"/>
    <path d="M380 512 Q440 300 660 190 L660 512 Z" fill="url(#blueField)"/>
    <path d="M580 160 L660 68 L660 108 L600 178 Z" fill="#6e6e6e"/>

    <circle cx="490" cy="123" r="119" fill="var(--blue)"/>
    <circle cx="490" cy="123" r="112" fill="url(#bodyTones)" role="img" aria-label="Before and after photos of a client flexing, showing a slimmer waist"/>
    <line x1="490" y1="11" x2="490" y2="235" stroke="#ffffff" stroke-width="2"/>
    <rect x="385" y="181" width="210" height="22" fill="#ffffff" fill-opacity="0.75"/>

    <circle cx="370" cy="369" r="100" fill="#666666"/>
    <circle cx="370" cy="369" r="93" fill="url(#gymTones)" role="img" aria-label="Photo of a client exercising on a ball while wearing a training suit, guided by a trainer"/>

    <circle cx="546" cy="369" r="98" fill="#666666"/>
    <circle cx="546" cy="369" r="91" fill="url(#portraitTones)" role="img" aria-label="Before and after photos of a client's weight loss"/>
    <line x1="546" y1="278" x2="546" y2="460" stroke="#ffffff" stroke-width="2"/>
    <rect x="460" y="408" width="172" height="20" fill="#ffffff" fill-opacity="0.75"/>

    <rect y="494" width="660" height="18" fill="var(--band)"/>
  </svg>

  <span class="label" style="left:412px;top:182px;">Before</span>
  <span class="label" style="left:508px;top:182px;">After</span>
  <span class="label" style="left:476px;top:408px;">Before</span>
  <span class="label" style="left:554px;top:408px;">After</span>

  <div class="brand"><span class="brand__dot"></span><span class="brand__name">COPPERLEAF STUDIO</span></div>
  <h2 class="claim claim--blue claim--1">UP TO 18 TIMES</h2>
  <div class="claim claim--blue claim--2">MORE EFFECTIVE</div>
  <div class="claim claim--dark claim--3">Than</div>
  <div class="claim claim--dark claim--4">a conventional</div>
  <div class="claim claim--dark claim--5">gym workout</div>

  <div class="contact-bar">Contact Today</div>
  <ul class="contact-list">
    <li>
      <svg width="12" height="12" viewBox="0 0 12 12"><path d="M2 1 L4.5 1 L5.2 3.5 L3.8 4.6 Q5 7.2 7.4 8.2 L8.5 6.8 L11 7.5 L11 10 Q5 11 1 3 Z" fill="var(--blue)"/></svg>
      <span>(555) 555-0137</span>
    </li>
    <li>
      <svg width="12" height="12" viewBox="0 0 12 12"><rect x="0.5" y="2.5" width="11" height="8" fill="var(--blue)"/><path d="M0.5 2.5 L6 7 L11.5 2.5" fill="none" stroke="#ffffff" stroke-width="1"/></svg>
      <span class="email">copperleafwellness@mailbox.example</span>
    </li>
    <li>
      <svg width="12" height="12" viewBox="0 0 12 12"><circle cx="6" cy="6" r="5.3" fill="none" stroke="var(--blue)" stroke-width="1.2"/><ellipse cx="6" cy="6" rx="2.3" ry="5.3" fill="none" stroke="var(--blue)" stroke-width="1"/><line x1="0.7" y1="6" x2="11.3" y2="6" stroke="var(--blue)" stroke-width="1"/></svg>
      <span>copperleaf-studio.example</span>
    </li>
    <li>
      <svg width="12" height="14" viewBox="0 0 12 14"><path d="M6 13.5 Q1 7.5 1 5 A5 5 0 0 1 11 5 Q11 7.5 6 13.5 Z" fill="var(--blue)"/><circle cx="6" cy="5" r="1.8" fill="#ffffff"/></svg>
      <span>287 Wendover Ln,<br>Building D Suite 318,<br>Fernhollow Bay 40512</span>
    </li>
  </ul>
</section>

</body>
</html>
```